Foot and ankle surgeon requires a website design

I need a website where prospective and established patients can obtain information and then direct them to making appointments. My practice is a highly professional surgical practice specialising in surgery to the foot and ankle. My title is Mr Colin Brasket, Podiatric Foot & Ankle Surgeon. My qualifications are: BSc MSc FACPS
The practice website will require information on: Locations, phone numbers to make appointments, general background on podiatric surgery,
I would like to include information on: my hospital appointments, surgical fellowships held, training programs undertaken, association memberships, publications written, links to useful websites
A page dedicated to common foot conditions would be useful and also a page with referral information including an online registration section that will be sent direct to the receptionist.
Examples of similar websites include:
http://www.dorvelquintaro.com.au/
http://www.haldenfootsurgeon.com.au/
I will provide files on logo, self photos and my personal training history etc.
Also if there is going to be a background theme I personally am associated with surfing and beach activities, it would be great if this was able to be reflected in the design.
Thank you.

```html
<!DOCTYPE html>
<html lang="en">
<head>
<meta charset="utf-8">
<title>Mr Colin Brasket – Podiatric Foot &amp; Ankle Surgeon</title>
<link rel="stylesheet" href="https://fonts.googleapis.com/css2?family=Ubuntu:wght@400;500&family=Open+Sans:wght@400;600&display=swap">
<style>
:root{
  --blue:#0d4a8a;
  --blue-dark:#0a3a70;
  --blue-deep:#08305e;
  --orange:#f7870f;
  --text:#555;
  --line:#dcdcdc;
  --bg:#f6f6f6;
}
*{box-sizing:border-box;margin:0;padding:0}
html,body{width:821px;height:1200px;overflow:hidden}
body{position:relative;background:var(--bg);font-family:"Open Sans",sans-serif;color:var(--text)}
.abs{position:absolute}
.topline{left:0;top:0;width:821px;height:5px;background:var(--blue)}
.brand{left:68px;top:38px;display:flex;align-items:center;gap:8px}
.brand-dot{width:20px;height:20px;border-radius:50%;background:var(--orange)}
.brand-name{font-family:"Ubuntu",sans-serif;font-weight:500;font-size:17px;color:var(--blue)}
.search{left:563px;top:40px;width:189px;height:29px;border:1px solid #ccc;background:#fff;font-size:11px;color:#333;padding:7px 8px}
.search svg{position:absolute;right:7px;top:7px}
.nav{left:68px;top:97px;width:684px;height:52px;background:var(--blue);display:flex;font-size:9px;color:#fff}
.nav a{display:flex;align-items:center;padding:0 15px;color:#fff;text-decoration:none;white-space:nowrap}
.nav a.active{background:var(--orange);width:66px;justify-content:center;padding:0}
.nav a:nth-child(n+2){flex:1;justify-content:center;padding:0}
.hero{left:68px;top:155px;width:684px;height:298px;background:linear-gradient(120deg,#e8d6cc 0%,#d9c3b6 40%,#c9c2bb 70%,#8a9a3a 92%,#a8452c 100%)}
.hero-tag{background:var(--blue);color:#fff;font-family:"Ubuntu",sans-serif;font-size:18px;display:flex;align-items:center;justify-content:center}
.hero-arrow{width:22px;height:22px;border-radius:50%;background:#fff;box-shadow:0 1px 3px rgba(0,0,0,.3);display:flex;align-items:center;justify-content:center}
.dots{left:387px;top:429px;display:flex;gap:6px}
.dots span{width:9px;height:9px;border-radius:50%;border:1.5px solid #fff;background:transparent}
.dots span.on{background:var(--blue);border-color:var(--blue)}
.info{top:462px;height:74px;color:#fff;padding:14px 10px 0}
.info h3{font-family:"Ubuntu",sans-serif;font-weight:500;font-size:13px;margin-bottom:5px}
.info h3 small{font-size:10px;font-weight:400}
.info p{font-size:8.2px;line-height:14px}
.info p a{color:var(--orange)}
.info.orange p a{color:var(--blue)}
.info.blue{background:var(--blue)}
.info.orange{background:var(--orange)}
.welcome{left:68px;top:553px;width:456px}
h2.section{font-family:"Ubuntu",sans-serif;font-weight:400;font-size:18px;color:var(--orange)}
.welcome p{margin-top:8px;font-size:8.3px;line-height:16.5px;text-align:justify}
.welcome p a{color:var(--blue)}
.fellow{left:543px;top:553px;width:205px;height:144px;background:#fff;border:1px solid #ccc;border-radius:4px;overflow:hidden}
.fellow h4{background:var(--blue);color:#fff;font-family:"Ubuntu",sans-serif;font-weight:500;font-size:11.5px;height:38px;padding:13px 10px 0}
.fellow ul{list-style:none;padding:0 10px}
.fellow li{font-size:8.6px;color:#333;height:23px;display:flex;align-items:center;gap:8px;border-bottom:1px solid #e5e5e5}
.fellow li:last-child{border:0}
.news-title{left:68px;top:716px}
.card{top:752px;width:229px;height:240px;background:#fff;border:1px solid #ddd}
.card .photo{width:100%;height:142px;position:relative}
.card .date{position:absolute;right:0;bottom:0;width:38px;height:43px;background:var(--blue);color:#fff;padding:5px 0 0 10px}
.card .date span{display:block;font-size:9px}
.card .date b{font-family:"Ubuntu",sans-serif;font-weight:400;font-size:14px}
.card h5{font-family:"Ubuntu",sans-serif;font-weight:400;font-size:11px;color:var(--blue);margin:9px 8px 6px}
.card p{font-size:8.1px;line-height:12.5px;margin:0 8px}
.card a{display:block;margin:4px 8px;font-size:8.1px;color:var(--orange);text-decoration:none}
.member{left:553px;top:753px;width:199px;height:119px;background:linear-gradient(135deg,#4a5568,#5d6b7d 50%,#3e4a5a)}
.member h4{position:absolute;top:32px;width:100%;text-align:center;color:#fff;font-family:"Ubuntu",sans-serif;font-weight:400;font-size:17px}
.member .btn{position:absolute;left:57px;top:64px;width:85px;height:24px;background:var(--orange);color:#fff;font-size:8.5px;display:flex;align-items:center;justify-content:center}
.newsletter{left:553px;top:882px;width:199px;height:110px;background:var(--blue);color:#fff;padding:10px 11px}
.newsletter h4{font-family:"Ubuntu",sans-serif;font-weight:400;font-size:12.5px}
.newsletter p{font-size:8px;margin-top:2px}
.newsletter .field{margin-top:9px;height:23px;background:#fff;border-radius:3px;color:#999;font-size:7.5px;padding:6px 7px}
.newsletter .send{position:absolute;right:11px;top:75px;width:52px;height:19px;background:var(--orange);border-radius:3px;font-size:8px;display:flex;align-items:center;justify-content:center}
.footer{left:0;top:1013px;width:821px;height:138px;background:var(--blue)}
.footer h4{position:absolute;color:#fff;font-family:"Ubuntu",sans-serif;font-weight:400;font-size:13px}
.contact{left:68px;top:40px;width:215px;color:#fff;font-size:8.6px;line-height:15.5px}
.contact b{font-weight:400;color:var(--orange)}
.social{position:absolute;left:669px;top:43px;display:flex;gap:6px}
.social span{width:16px;height:16px;border-radius:2px}
.bottombar{left:0;top:1151px;width:821px;height:49px;background:var(--blue-deep);color:#fff;font-size:8.6px;display:flex;align-items:center;justify-content:center}
</style>
</head>
<body>
<div class="abs topline"></div>

<div class="abs brand"><span class="brand-dot"></span><span class="brand-name">Mr Colin Brasket</span></div>

<div class="abs search">Search
  <svg width="14" height="14" viewBox="0 0 14 14"><circle cx="5.5" cy="5.5" r="4.3" fill="none" stroke="#111" stroke-width="1.8"/><line x1="8.6" y1="8.6" x2="13" y2="13" stroke="#111" stroke-width="2"/></svg>
</div>

<nav class="abs nav">
  <a class="active">Home</a><a>Appointments</a><a>surgical fellowships</a><a>training programs</a><a>memberships</a><a>publications</a><a>useful websites</a><a>contact us</a>
</nav>

<div class="abs hero" role="img" aria-label="Photo of a podiatric surgeon treating a patient's foot with gloved hands"></div>
<div class="abs hero-tag" style="left:133px;top:274px;width:168px;height:39px">Podiatric Surgery</div>
<div class="abs hero-tag" style="left:218px;top:320px;width:147px;height:39px">Treatment</div>
<div class="abs hero-arrow" style="left:88px;top:289px"><svg width="8" height="10"><path d="M6 1L2 5l4 4" fill="none" stroke="#333" stroke-width="2"/></svg></div>
<div class="abs hero-arrow" style="left:703px;top:289px"><svg width="8" height="10"><path d="M2 1l4 4-4 4" fill="none" stroke="#333" stroke-width="2"/></svg></div>
<div class="abs dots"><span class="on"></span><span></span><span></span></div>

<div class="abs info blue" style="left:68px;width:222px"><h3>Locations</h3><p>Lorem ipsum dolor sit amet, consectetur adipiscing elit, sed do eiusmod tempor <a>here</a></p></div>
<div class="abs info orange" style="left:300px;width:221px"><h3><small>make</small> Appointments</h3><p>Lorem ipsum dolor sit amet, consectetur adipiscing elit, sed do eiusmod tempor <a>here</a></p></div>
<div class="abs info blue" style="left:530px;width:222px"><h3>Phone</h3><p>Lorem ipsum dolor sit amet, consectetur adipiscing elit, sed do eiusmod tempor <a>here</a></p></div>

<section class="abs welcome">
  <h2 class="section">Welcome To Our Website</h2>
  <p>Lorem ipsum dolor sit amet, consectetuer adipiscing elit, sed diam nonummy nibh euismod tincidunt ut laoreet dolore magna aliquam erat volutpat. Ut wisi enim ad minim veniam, quis nostrud exerci tation ullamcorper suscipit lobortis nisl ut aliquip ex ea commodo consequat. Duis autem vel eum iriure dolor in hendrerit in vulputate velit esse molestie consequat, vel illum dolore eu feugiat nulla facilisis at vero eros et accumsan et iusto odio dignissim qui blandit praesent luptatum zzril delenit augue duis dolore te feugait nulla facilisi. Nam liber tempor cum soluta nobis eleifend option congue nihil imperdiet doming id quod mazim placerat facer possim assum. Ut wisi enim ad minim veniam, quis nostrud exerci tation ullamcorper suscipit lobortis nisl. <a>Read more...</a></p>
</section>

<aside class="abs fellow">
  <h4>Surgical fellowships</h4>
  <ul>
    <li><svg width="10" height="8"><path d="M1 4l3 3 5-6" fill="none" stroke="#f7870f" stroke-width="1.6"/></svg>Shutdowns and Remote Projects</li>
    <li><svg width="10" height="8"><path d="M1 4l3 3 5-6" fill="none" stroke="#f7870f" stroke-width="1.6"/></svg>Working at Heights Projects</li>
    <li><svg width="10" height="8"><path d="M1 4l3 3 5-6" fill="none" stroke="#f7870f" stroke-width="1.6"/></svg>Confined Space Projects</li>
    <li><svg width="10" height="8"><path d="M1 4l3 3 5-6" fill="none" stroke="#f7870f" stroke-width="1.6"/></svg>Environmentally Sensitive Projects</li>
  </ul>
</aside>

<h2 class="abs section news-title">Latest News</h2>

<article class="abs card" style="left:68px">
  <div class="photo" role="img" aria-label="Photo of an open foot surgery with instruments" style="background:linear-gradient(135deg,#3a2a22,#8a4a3a 45%,#c48a70 65%,#2a2622)">
    <div class="date"><span>Sun</span><b>12</b></div>
  </div>
  <h5>Lorem ispum</h5>
  <p>Lorem ipsum dolor sit amet, consectetuer adipiscing elit, sed diam nonummy nibh euismod tincidunt ut laoreet dolore magna aliquam erat volutpat.</p>
  <a>Read More...</a>
</article>

<article class="abs card" style="left:314px">
  <div class="photo" role="img" aria-label="Photo of a bandaged foot after surgery" style="background:linear-gradient(90deg,#1a1a1a 0%,#2b2a22 30%,#e9c98a 50%,#d9b070 65%,#2e8a5a 90%,#1c1c1c)">
    <div class="date"><span>Sun</span><b>12</b></div>
  </div>
  <h5>Lorem ipsum</h5>
  <p>Lorem ipsum dolor sit amet, consectetuer adipiscing elit, sed diam nonummy nibh euismod tincidunt ut laoreet dolore magna aliquam erat volutpat.</p>
  <a>Read More...</a>
</article>

<div class="abs member" role="img" aria-label="Photo of surgeons in an operating theatre">
  <h4>Membership</h4>
  <div class="btn">CLICK HERE</div>
</div>

<div class="abs newsletter">
  <h4>NewsLetters</h4>
  <p>Lorem ipsum dolor sit amet, consectetur</p>
  <div class="field">Email</div>
  <div class="send">Send</div>
</div>

<footer class="abs footer">
  <h4 style="left:68px;top:20px">Contact Us</h4>
  <div class="abs contact">
    <b>Seacliff:</b> 42 Harbour View Road PO Box 1187, Seacliff WA 6531<br>
    <b>Ph:</b> 08 9100 2231 &nbsp;<b>Fax:</b> 08 9100 2232<br>
    <b>Ridgeford:</b> 7/14 Dunmore Street PO Box 20318, Ridgeford WA 6431<br>
    <b>Ph:</b> 08 9100 3341 &nbsp;<b>Fax:</b> 08 9100 3342
  </div>
  <h4 style="left:668px;top:20px;font-weight:500">Follow Us</h4>
  <div class="social">
    <span style="background:#3b5b9a"></span><span style="background:#3fa9dd"></span><span style="background:#1c7bb4"></span><span style="background:#f7870f"></span>
  </div>
</footer>

<div class="abs bottombar">© 2014 Company Name &nbsp;All right reserved &nbsp;Term of Use</div>
</body>
</html>
```